sydney wedding photography business needs a business card design

we need a business card design for a sydney based wedding photography and videography business. our business name is :golden hour studio and film. our target clients are 24-35 yrs female. our style is candid, organic, natural, dynamic. we are a team of young photographers and videographers, and help brides to create memories that they will cherish for the rest of their lives. the logo will be provided. we want an elegant design that reflects our style, and also want to give a great impression to our clients that we are one of the best studios in sydney and our brand means quality and premium service.

Target Market(s)

bride to be, 24-35 years old, living in sydney and surrunding areas

Industry/Entity Type

Wedding Photography

Contact Information for Business Card

address: 57 tarrant street, glenmore nsw 2047
mobile: 0431872259
phone: (02) 9163 2408
info@tidewillowstudio.net.au
www.tidewillowstudio.net.au
facebook:tidewillowweddings
instagram:tidewillowweddings

Font styles to use
Serif
Sans Serif

Requirements
Nice to have
• maybe add my slogan"memories beyond eternity" if the layout looks good
Should not have
• no black color, not good idea for wedding biz card

```html
<!DOCTYPE html>
<html lang="en">
<head>
<meta charset="utf-8">
<title>Golden Hour Studio and Film – Business Card</title>
<link rel="stylesheet" href="https://fonts.googleapis.com/css2?family=Open+Sans:wght@400;600;700&display=swap">
<style>
  :root {
    --gold-deep: #d29f10;
    --gold-bright: #f3c20a;
    --gold-text: #c8950f;
    --paper: #ffffff;
    --backdrop: #efe9dd;
    --card-shadow: rgba(90, 60, 10, 0.22);
  }
  * { box-sizing: border-box; margin: 0; padding: 0; }
  html, body { width: 1200px; height: 900px; overflow: hidden; }
  body {
    background: var(--backdrop);
    font-family: "Open Sans", Arial, sans-serif;
    display: flex;
    flex-direction: column;
    align-items: center;
    justify-content: center;
    gap: 44px;
  }
  .card {
    width: 700px;
    height: 400px;
    position: relative;
    overflow: hidden;
    box-shadow: 0 10px 30px var(--card-shadow);
  }
  .card--front {
    background: linear-gradient(180deg, var(--gold-deep) 0%, var(--gold-bright) 100%);
    display: flex;
    align-items: center;
    justify-content: center;
  }
  .brand {
    text-align: center;
    font-weight: 700;
    font-size: 46px;
    line-height: 1.05;
    color: var(--paper);
    letter-spacing: 0.5px;
  }
  .card--back { background: var(--paper); }
  .card--back .brand-area {
    height: 42%;
    display: flex;
    align-items: center;
    justify-content: flex-end;
    padding-right: 90px;
  }
  .card--back .brand { color: var(--gold-text); font-size: 38px; }
  .info-band {
    position: absolute;
    left: 0; right: 0; bottom: 0;
    height: 58%;
    background: linear-gradient(180deg, var(--gold-deep) 0%, var(--gold-bright) 100%);
    color: var(--paper);
  }
  .contact-list {
    position: absolute;
    right: 34px;
    top: 26px;
    list-style: none;
    text-align: right;
    font-size: 15px;
    line-height: 24px;
  }
  .contact-list li { display: flex; align-items: center; justify-content: flex-end; gap: 7px; }
  .contact-list svg { width: 12px; height: 12px; fill: var(--paper); }
  .person {
    position: absolute;
    left: 60px;
    bottom: 44px;
  }
  .person-name { font-size: 22px; font-weight: 700; }
  .person-role { font-size: 17px; margin-bottom: 14px; }
  .person-address { font-size: 18px; line-height: 25px; font-style: normal; }
</style>
</head>
<body>
  <section class="card card--front" aria-label="Card front">
    <p class="brand">Golden Hour<br>Studio and Film</p>
  </section>

  <section class="card card--back" aria-label="Card back">
    <div class="brand-area">
      <p class="brand">Golden Hour<br>Studio and Film</p>
    </div>
    <div class="info-band">
      <ul class="contact-list">
        <li>(02) 9163 2408
          <svg viewBox="0 0 12 12" aria-hidden="true"><path d="M2.5 1l2 2-1 1.5c.7 1.5 1.6 2.4 3 3L8 6.5l2 2-1.2 1.8C5 10 2 7 1.7 3.2z"/></svg></li>
        <li>info@tidewillowstudio.net.au
          <svg viewBox="0 0 12 12" aria-hidden="true"><path d="M1 2.5h10v7H1z M1.5 3l4.5 3.5L10.5 3" stroke="#d29f10" stroke-width="0.9"/></svg></li>
        <li>www.tidewillowstudio.net.au
          <svg viewBox="0 0 12 12" aria-hidden="true"><circle cx="6" cy="6" r="5"/><path d="M1 6h10M6 1c-2 2.8-2 7.2 0 10M6 1c2 2.8 2 7.2 0 10" fill="none" stroke="#d29f10" stroke-width="0.8"/></svg></li>
      </ul>
      <div class="person">
        <p class="person-name">Claire Whitmore</p>
        <p class="person-role">Managing Director</p>
        <address class="person-address">57 Tarrant Street,<br>Glenmore NSW 2047</address>
      </div>
    </div>
  </section>
</body>
</html>
```